Firm Stationery Design

I need a design for stationery, including: Stationery First Page, Stationery Second Sheet, Envelope, Mailing Label for Flat Envelopes, and Business Cards

```html
<!DOCTYPE html>
<html lang="en">
<head>
<meta charset="utf-8">
<title>Harland Law LLC — Business Card</title>
<link href="https://fonts.googleapis.com/css2?family=Montserrat:wght@400;500;600;700&display=swap" rel="stylesheet">
<style>
  :root {
    --page-bg: #e9e3da;
    --card-bg: #f4f1ec;
    --card-edge: #ffffff;
    --ink-dark: #333333;
    --ink-text: #2e2b28;
    --accent: #d98a1f;
  }
  * { box-sizing: border-box; margin: 0; padding: 0; }
  html, body {
    width: 1200px;
    height: 1047px;
    overflow: hidden;
    background: var(--page-bg);
    font-family: "Montserrat", sans-serif;
  }
  .card {
    position: absolute;
    left: 150px;
    top: 290px;
    width: 948px;
    height: 518px;
    background: var(--card-bg);
    border: 2px solid var(--card-edge);
    border-radius: 24px;
    box-shadow: 0 10px 30px rgba(0,0,0,0.08);
  }
  .brand {
    position: absolute;
    left: 110px;
    top: 115px;
    width: 330px;
    text-align: center;
  }
  .brand-mark {
    display: block;
    width: 130px;
    height: 130px;
    margin: 0 auto 40px;
    background: var(--accent);
  }
  .brand-name {
    font-weight: 700;
    font-size: 56px;
    line-height: 1;
    letter-spacing: 1px;
    color: var(--ink-dark);
    white-space: nowrap;
  }
  .brand-sub {
    margin-top: 24px;
    font-weight: 600;
    font-size: 24px;
    line-height: 1;
    letter-spacing: 14px;
    padding-left: 14px;
    color: var(--accent);
    white-space: nowrap;
  }
  .divider {
    position: absolute;
    left: 458px;
    top: 117px;
    width: 3px;
    height: 280px;
    background: var(--accent);
  }
  .details {
    position: absolute;
    left: 495px;
    top: 108px;
    color: var(--ink-text);
  }
  .person-name {
    font-weight: 600;
    font-size: 36px;
    letter-spacing: 0.5px;
    color: var(--accent);
    line-height: 1.1;
    white-space: nowrap;
  }
  .person-title {
    font-weight: 400;
    font-size: 26px;
    line-height: 1.2;
    margin-top: 6px;
  }
  .address {
    font-size: 26px;
    line-height: 36px;
    margin-top: 24px;
  }
  .contact-list {
    list-style: none;
    margin-top: 18px;
  }
  .contact-item {
    display: flex;
    align-items: center;
    font-size: 26px;
    line-height: 36px;
    white-space: nowrap;
  }
  .contact-icon {
    width: 20px;
    height: 20px;
    margin-right: 12px;
    flex: none;
  }
</style>
</head>
<body>
  <div class="card">
    <div class="brand">
      <span class="brand-mark"></span>
      <div class="brand-name">HARLAND</div>
      <div class="brand-sub">LAW LLC</div>
    </div>

    <div class="divider"></div>

    <div class="details">
      <div class="person-name">DANIEL WHITMORE</div>
      <div class="person-title">Managing Director</div>
      <div class="address">Your address, City<br>State, Zip 1234</div>
      <ul class="contact-list">
        <li class="contact-item">
          <svg class="contact-icon" viewBox="0 0 20 20" aria-hidden="true">
            <path fill="#d98a1f" d="M2 7c0-2 3-4 8-4s8 2 8 4v2h-4V7.5c-1-.6-2.4-.9-4-.9s-3 .3-4 .9V9H2z"/>
            <rect x="4" y="10" width="12" height="7" rx="1.5" fill="#d98a1f"/>
            <circle cx="10" cy="13.5" r="1.8" fill="#f4f1ec"/>
          </svg>
          123 456 789
        </li>
        <li class="contact-item">
          <svg class="contact-icon" viewBox="0 0 20 20" aria-hidden="true">
            <rect x="2" y="5" width="16" height="11" rx="1" fill="#d98a1f"/>
            <path d="M2.5 5.5 10 11l7.5-5.5" fill="none" stroke="#f4f1ec" stroke-width="1.4"/>
          </svg>
          info@yourmail.com
        </li>
        <li class="contact-item">
          <svg class="contact-icon" viewBox="0 0 20 20" aria-hidden="true">
            <circle cx="10" cy="10" r="8" fill="#d98a1f"/>
            <ellipse cx="10" cy="10" rx="3.5" ry="8" fill="none" stroke="#f4f1ec" stroke-width="1.2"/>
            <path d="M2 10h16M3.5 6h13M3.5 14h13" stroke="#f4f1ec" stroke-width="1.2"/>
          </svg>
          www.yourwebsite.com
        </li>
      </ul>
    </div>
  </div>
</body>
</html>
```